Maple Beacon Website

We are starting a marketing company and to do that we need a website! We want a website that will inspire and persuade to bring out the awesomeness in our clients.
What we want to see:
- Inspirational and persuasive imagery that relate to Branding.
- No cliche images eg. business man, suits and hand shakes
- We want to transform and educate our clients.
- We want to show them the path and would like our website to really act as a guide that guides them step by step through our process.
- We want the portray that we are an investment but not have a pretentious way to it. We put our heart into every project and that is how we treat our clients.
-When you submit your design please include what platform you have created for. Preference would be Wordpress or Joobla.

We have included the psd file for the wire frame, logo files, font files, site map and a link to a video we create to give you more information on what we would like to see. http://clipvault.example/t/qk82LmZpr

Feel free to make small modification to the logos if you think it will improve it. Your creativity and advice is most welcome.
Updates

One thing we forgot. We would like to have our contact information near the top of the website as well as at the bottom.  Here is out contact info:

Email: info@maplebeacon.example
Phone: 587-555-0142

Project Deadline Extended
Reason: As we are new with the platform and that we want to optimize our results, we decided to extend the deadline by 15 days. Thanks!

Target Market(s)

28-60, Male and Female, Oil field, Local Businesses, Dentists, Chiropractors, Hair salon, Construction/Renovation, Events etc

Industry/Entity Type

Investment

Requirements
Must have
• - 4 Inspirational and persuasive Imagery for the top portion of the website
- Must have a feel as if your not on a website an example of this is linked below.
http://www.artbidhub.example/design/402957/web-design-by-lena-torvik
Nice to have
• - Creative advice from you.
- Creative buttons for Get Free Quote and Subscribe buttons. Something out of the box that draws peoples attention. eg. a 'B' button. Just and example but still something related to branding.
Should not have
• No Cliches

```html
<!DOCTYPE html>
<html lang="en">
<head>
<meta charset="utf-8">
<title>Maple Beacon</title>
<link rel="stylesheet" href="https://fonts.googleapis.com/css2?family=Open+Sans:ital,wght@0,400;0,600;0,700;1,600&family=Sansita:wght@700;800&display=swap">
<style>
:root{
  --page:#f7f7f7;
  --ink:#333;
  --body:#666;
  --green:#8dc63f;
  --green-text:#5a8f1e;
  --tab:#7c7c7c;
  --tab-line:#9a9a9a;
  --white:#fff;
  --sky-deep:#1583dc;
  --sky-light:#5fb0ee;
}
*{box-sizing:border-box;margin:0;padding:0}
html,body{width:1200px;height:952px;overflow:hidden;background:var(--page);font-family:"Open Sans",sans-serif;color:var(--body)}
.canvas{position:relative;width:1200px;height:952px;overflow:hidden}
.contact{display:flex;align-items:center;gap:6px;color:#eee;font-size:16px}
.contact strong{color:var(--white);font-weight:700}
.contact svg{width:14px;height:14px;fill:#222}
.topbar{position:absolute;left:0;top:0;width:1200px;height:38px;background:linear-gradient(#b5b5b5,#3a3a3a);display:flex;justify-content:flex-end;align-items:center;padding-right:175px}
.header{position:absolute;left:170px;top:50px;width:857px;height:339px;border:1px solid #ddd}
.side{position:absolute;left:0;top:0;width:206px;height:273px;background:linear-gradient(160deg,#f4f4f4 35%,#a9cfe8 80%,#5ca6dc)}
.brand{position:absolute;left:14px;top:22px;display:flex;align-items:center;gap:8px}
.brand-dot{width:16px;height:16px;border-radius:50%;background:var(--green)}
.brand-name{font-size:24px;font-weight:700;color:#666;line-height:1}
.tagline{position:absolute;left:38px;top:74px;font-size:12px;font-style:italic;font-weight:600;color:#444}
.nav{position:absolute;left:15px;top:118px;list-style:none}
.nav li{font-size:14.5px;font-weight:700;color:#333;height:33.5px;letter-spacing:.2px}
.hero{position:absolute;left:206px;top:0;width:651px;height:273px;background:linear-gradient(100deg,var(--sky-deep),var(--sky-light) 75%,#a9bccb)}
.tabs{position:absolute;left:0;top:273px;width:857px;height:66px;display:flex;background:var(--tab)}
.tab-cta{width:206px;background:linear-gradient(#8fcb3f,#47821c);color:var(--white);font-family:"Sansita",sans-serif;font-weight:800;font-size:22px;line-height:21px;text-align:center;display:flex;align-items:center;justify-content:center}
.step{position:relative;flex:1;border-left:1px solid var(--tab-line);color:var(--white);font-family:"Sansita",sans-serif;font-weight:700;font-size:16px;display:flex;align-items:center;justify-content:center;letter-spacing:.2px}
.step::before{content:"";position:absolute;top:-9px;left:50%;margin-left:-9px;width:14px;height:14px;border-radius:50%;background:radial-gradient(circle at 40% 35%,#ddd,#666);border:2px solid #eee}
.step.active{color:var(--green)}
.step.active::before{background:radial-gradient(circle at 40% 35%,#c9ef8a,#5e9d1e)}
.social{position:absolute;left:171px;top:403px;display:flex;gap:8px}
.social-btn{width:45px;height:45px;border-radius:3px;background:linear-gradient(#6a6a6a,#2b2b2b);display:flex;align-items:center;justify-content:center}
.social-btn::before{content:"";width:14px;height:14px;border-radius:50%;background:var(--white)}
.tips{position:absolute;left:389px;top:406px}
.tips h3{font-size:21px;font-weight:700;color:var(--green);line-height:1.1}
.tips p{font-size:15px;font-weight:700;color:#555}
.email-field{position:absolute;left:620px;top:409px;width:301px;height:36px;border:1px solid #ccc;border-radius:2px;background:linear-gradient(#f5f5f5,#fff);font-size:12.5px;color:#555;padding:9px 8px}
.btn-subscribe{position:absolute;left:927px;top:409px;width:100px;height:36px;border-radius:3px;background:linear-gradient(#c8c8c8,#7d7d7d);color:var(--white);font-weight:700;font-size:15px;display:flex;align-items:center;justify-content:center}
.rule{position:absolute;left:175px;top:461px;width:848px;border-top:1px dashed #bbb}
.content{position:absolute;left:173px;top:484px;width:830px}
.content h1{font-family:"Sansita",sans-serif;font-weight:800;font-size:21px;color:var(--ink);margin-left:1px}
.content h2{font-size:14px;font-weight:700;color:var(--green-text);margin:10px 0 0 3px}
.content p{font-size:13.7px;line-height:19px;margin-left:3px}
.checks{list-style:none;margin:10px 0 0 4px}
.checks li{display:flex;align-items:center;gap:10px;height:31px;font-size:13.7px;color:#444}
.checks svg{width:17px;height:17px}
.content p.closing{margin-top:15px}
.btn-quote{position:absolute;left:884px;top:708px;width:141px;height:36px;border-radius:3px;background:linear-gradient(#7fbe35,#3f7b19);color:var(--white);font-weight:700;font-size:14.5px;display:flex;align-items:center;justify-content:center;border:1px solid #3a7015}
.footer{position:absolute;left:0;top:844px;width:1200px;height:108px;background:linear-gradient(#a6a6a6,#2e2e2e)}
.footer-links{position:absolute;left:174px;top:28px;display:flex;gap:12px;font-size:15px;color:var(--white)}
.copyright{position:absolute;left:174px;top:53px;font-size:15px;color:var(--green)}
.footer .contact{position:absolute;right:175px;top:30px}
</style>
</head>
<body>
<div class="canvas">
  <div class="topbar">
    <div class="contact">
      <svg viewBox="0 0 16 16"><path d="M1 3h14v10H1z M1 3l7 6 7-6" stroke="#eee" stroke-width="1"/></svg>
      <span>info@maplebeacon.example</span> | 
      <svg viewBox="0 0 16 16"><path d="M3 1l3 1 1 3-2 1c1 2 3 4 5 5l1-2 3 1 1 3-2 2C7 14 2 9 1 3z"/></svg>
      <strong>587-555-0142</strong>
    </div>
  </div>

  <header class="header">
    <div class="side">
      <div class="brand"><span class="brand-dot"></span><span class="brand-name">Maple Beacon</span></div>
      <div class="tagline">Because You're Awesome!</div>
      <ul class="nav">
        <li>STRATEGY</li><li>PORTFOLIO</li><li>ABOUT US</li><li>CONTACT US</li><li>BLOG</li>
      </ul>
    </div>
    <div class="hero" role="img" aria-label="Photo of a climber rappelling down a sunlit cliff beside a snowy mountain under a blue sky"></div>
    <nav class="tabs">
      <div class="tab-cta">CONNECT<br>WITH US</div>
      <div class="step">MAPLE BEACON</div>
      <div class="step">BE FOUND</div>
      <div class="step">CONNECT</div>
      <div class="step active">GET GROWING</div>
    </nav>
  </header>

  <div class="social" aria-label="Social links"><span class="social-btn"></span><span class="social-btn"></span><span class="social-btn"></span><span class="social-btn"></span></div>
  <div class="tips"><h3>GET TIPS AND TRICKS!</h3><p>Subscribe to our Newsletter.</p></div>
  <div class="email-field">your email id</div>
  <div class="btn-subscribe">Subscribe</div>
  <div class="rule"></div>

  <main class="content">
    <h1>WELCOME TO MAPLE BEACON</h1>
    <h2>Our Mission</h2>
    <p>Etiam adipiscing mollis nulla, ac bibendum elit commodo ac. Pellentesque vehicula sodales vulputate. Suspendisse vel semper tortor. Duis tristique pharetra ligula sed bibendum. Etiam adipiscing mollis nulla, ac bibendum elit commodo ac. Etiam adipiscing mollis nulla, ac bibendum elit commodo ac.</p>
    <ul class="checks">
      <li><svg viewBox="0 0 17 17"><rect width="17" height="17" rx="3" fill="#8dc63f"/><path d="M4 9l3 3 6-7" stroke="#fff" stroke-width="2.2" fill="none"/></svg>Nam ac risus metus, sit amet blandit ante.</li>
      <li><svg viewBox="0 0 17 17"><rect width="17" height="17" rx="3" fill="#8dc63f"/><path d="M4 9l3 3 6-7" stroke="#fff" stroke-width="2.2" fill="none"/></svg>Nunc adipiscing, ipsum eu scelerisque euismod, diam nisl condimentum neque,</li>
      <li><svg viewBox="0 0 17 17"><rect width="17" height="17" rx="3" fill="#8dc63f"/><path d="M4 9l3 3 6-7" stroke="#fff" stroke-width="2.2" fill="none"/></svg>Vel gravida ligula velit vitae nisl. Pellentesque at dignissim ipsum. Vivamus id massa arcu.</li>
      <li><svg viewBox="0 0 17 17"><rect width="17" height="17" rx="3" fill="#8dc63f"/><path d="M4 9l3 3 6-7" stroke="#fff" stroke-width="2.2" fill="none"/></svg>Phasellus feugiat condimentum neque ac bibendum.</li>
      <li><svg viewBox="0 0 17 17"><rect width="17" height="17" rx="3" fill="#8dc63f"/><path d="M4 9l3 3 6-7" stroke="#fff" stroke-width="2.2" fill="none"/></svg>Pellentesque dictum lectus sapien, eu pulvinar eros.</li>
    </ul>
    <p class="closing">Maecenas lacinia, nulla at interdum dapibus, velit sapien posuere eros, et hendrerit purus erat quis est. Proin commodo blandit mauris sed convallis. Donec tellus metus, feugiat sed condimentum congue, dignissim ut leo.</p>
  </main>
  <div class="btn-quote">Get a Free Quote!</div>

  <footer class="footer">
    <div class="footer-links"><span>Site Map</span><span>Strategy</span><span>Portfolio</span><span>About Us</span><span>Contact Us</span><span>Blog</span></div>
    <div class="copyright">©MAPLE BEACON INC. 2013</div>
    <div class="contact">
      <svg viewBox="0 0 16 16"><path d="M1 3h14v10H1z M1 3l7 6 7-6" stroke="#eee" stroke-width="1"/></svg>
      <span>info@maplebeacon.example</span> | 
      <svg viewBox="0 0 16 16"><path d="M3 1l3 1 1 3-2 1c1 2 3 4 5 5l1-2 3 1 1 3-2 2C7 14 2 9 1 3z"/></svg>
      <strong>587-555-0142</strong>
    </div>
  </footer>
</div>
</body>
</html>
```